Popup Nightclub Grand Opening Flyer

We need to design a flyer for the grand opening of an upscale, exclusive nightclub called "Lantern". The design needs to be chic and exclusive. The background should be black and the text should primarily be white. We like minimalist designs.

Here is the text for the flyer
-
Velvetroll Atlanta Presents

Lantern (LOGO)

A Popup Nightclub Experience
For one night Only

Friday, October 18, 2013
Party begins at 9PM

INVITE ONLY

See invitation for location details
(Velvetroll Atlanta logo)

-
Examples we like

http://cdn4-x.pressfolio-example.com/sites/default/files/styles/image_content_width/hash/3b/fd/2468013579_4421_flyer.jpg?itok=K9rtQw2z

http://files.hubspace-example.net/files/8Hqq-Tr72WWE3kaRbTmcxP5QZK2F396J8nbRw4CKMHfdX2Y7qSEF-MqjxDoNrLY3QCyQJD7npjGaRq3k-Mhx6hqf3MDSWf8r3/2zenSaturdays.jpg

http://morvex-example.com/wp-content/uploads/siteskin/widgetkit/gallery/2zen/2zen-gen_qstay4-01.jpg

Hi All, one thing that we are seeing that we don't like is on over emphasis on the phrase "a popup nightclub experience" please don't make this the largest thing on the flyer

Target Market(s)

Target market is 25-35 year olds who are affluent (rich) and like luxury brands

Requirements
Must have
• Dark Background
Nice to have
• Velvetroll Logo on the bottom
Modern text that isn't curvy
Should not have
• Curved text

```html
<!DOCTYPE html>
<html lang="en">
<head>
<meta charset="utf-8">
<title>Lantern Nightclub – A Popup Nightclub Experience</title>
<link rel="stylesheet" href="https://fonts.googleapis.com/css2?family=Montserrat:wght@600;700&family=Raleway:wght@300;400&display=swap">
<style>
  :root {
    --ink: #000000;
    --white: #ffffff;
    --yellow: #f2e600;
    --yellow-glow: rgba(242, 230, 0, 0.55);
    --grey: #9c9c9c;
    --rule: #8a8a8a;
    --silver-light: #d9dcdc;
    --silver-mid: #8e9393;
    --silver-dark: #3e4242;
    --bokeh-light: rgba(200, 200, 200, 0.55);
    --bokeh-mid: rgba(110, 110, 110, 0.35);
  }
  html, body {
    margin: 0;
    padding: 0;
    background: var(--ink);
    overflow: hidden;
  }
  .flyer {
    position: relative;
    width: 787px;
    height: 1200px;
    background: var(--ink);
    overflow: hidden;
    font-family: "Montserrat", Arial, sans-serif;
    color: var(--white);
  }
  .bokeh {
    position: absolute;
    inset: 0 0 300px 0;
    background:
      radial-gradient(ellipse 260px 220px at 700px 170px, var(--bokeh-light), transparent 70%),
      radial-gradient(ellipse 240px 280px at 70px 560px, var(--bokeh-light), transparent 72%),
      radial-gradient(ellipse 200px 260px at 700px 420px, var(--bokeh-mid), transparent 70%),
      radial-gradient(ellipse 220px 200px at 240px 140px, var(--bokeh-mid), transparent 70%),
      radial-gradient(ellipse 320px 220px at 300px 640px, rgba(120, 120, 120, 0.3), transparent 70%);
  }
  .emblem {
    position: absolute;
    top: 135px;
    left: 185px;
    width: 404px;
    height: 460px;
    border-radius: 50%;
    background: radial-gradient(circle at 30% 35%, var(--silver-light), var(--silver-mid) 45%, var(--silver-dark) 100%);
  }
  .line {
    position: absolute;
    left: 0;
    width: 100%;
    margin: 0;
    text-align: center;
    line-height: 1;
    white-space: nowrap;
  }
  .presenter {
    top: 52px;
    font-size: 24px;
    font-weight: 700;
    color: var(--yellow);
    text-shadow: 0 0 8px var(--yellow-glow);
  }
  .club-name {
    top: 688px;
    font-family: "Raleway", Arial, sans-serif;
    font-weight: 300;
    font-size: 58px;
    letter-spacing: 10px;
    padding-left: 10px;
  }
  .club-type {
    top: 757px;
    font-family: "Raleway", Arial, sans-serif;
    font-weight: 400;
    font-size: 29px;
    letter-spacing: 5px;
    padding-left: 5px;
  }
  .tagline {
    top: 822px;
    font-size: 32px;
    font-weight: 700;
  }
  .rule {
    position: absolute;
    top: 864px;
    left: 100px;
    width: 587px;
    height: 1px;
    background: var(--rule);
  }
  .one-night {
    top: 876px;
    font-size: 50px;
    font-weight: 700;
    color: var(--yellow);
    text-shadow: 0 0 14px var(--yellow-glow);
  }
  .date {
    top: 944px;
    font-size: 28px;
    font-weight: 700;
    color: var(--grey);
    letter-spacing: 2px;
  }
  .access {
    top: 1010px;
    font-size: 25px;
    font-weight: 700;
  }
  .location-note {
    top: 1054px;
    font-size: 12px;
    font-weight: 700;
  }
  .host {
    position: absolute;
    top: 1098px;
    left: 0;
    width: 100%;
    display: flex;
    justify-content: center;
    align-items: center;
    gap: 14px;
  }
  .host-dot {
    width: 40px;
    height: 40px;
    border-radius: 50%;
    background: var(--white);
  }
  .host-name {
    font-family: "Raleway", Arial, sans-serif;
    font-weight: 400;
    color: var(--white);
    text-align: left;
    line-height: 1;
  }
  .host-name .brand {
    display: block;
    font-size: 34px;
    letter-spacing: 1px;
  }
  .host-name .city {
    display: block;
    font-size: 11px;
    letter-spacing: 3px;
    margin-top: 4px;
  }
</style>
</head>
<body>
  <main class="flyer">
    <div class="bokeh" role="img" aria-label="Soft out-of-focus grey bokeh lights on black"></div>
    <div class="emblem" role="img" aria-label="Lantern nightclub emblem in polished silver"></div>

    <p class="line presenter">VELVETROLL ATLANTA PRESENTS</p>

    <h1 class="line club-name">LANTERN</h1>
    <p class="line club-type">NIGHTCLUB</p>

    <p class="line tagline">A POPUP NIGHTCLUB EXPERIENCE</p>
    <div class="rule"></div>
    <p class="line one-night">FOR ONE NIGHT ONLY</p>
    <p class="line date">FRIDAY OCTOBER 18 2013 @ 9:00PM</p>

    <p class="line access">INVITE ONLY</p>
    <p class="line location-note">SEE INVITATION FOR LOCATION DETAILS</p>

    <div class="host">
      <span class="host-dot"></span>
      <span class="host-name">
        <span class="brand">VELVETROLL</span>
        <span class="city">ATLANTA</span>
      </span>
    </div>
  </main>
</body>
</html>
```